WTF!!! We need a modern professional website for a business litigation law firm.

We need a modern, clean, professional and uncomplicated website for a new business trial and litigation law firm called "Haverlock Trial Firm PLLC". Website must be mobile optimized for iPad and smartphone. The law firm specializes in counseling and representing large corporations, small businesses and entrepreneurs in and out of the courtroom. Lawyers in the firm serve as Florida counsel and trial counsel to organizations facing claims involving product liability, premises liability, professional liability, vehicle and transportation liability, warranty claims, construction defects and delay claims, complex business disputes, commercial litigation and bid disputes in State and Federal Courts. The website is mainly to provide information about the firm, and should include sections describing the firm, identifying the Industries Served and Areas of Practice ," a separate page identifying the "Professionals", a separate page for "Resources & Advisories," and a traveling "Connect With Us" button a site visitor can click on that will launch an email to the Firm's general email account. The website should allow us to easily modify the content on these pages, and let us add/modify links to external information sources. We will not sell anything or take payments through the website. We do need to be able to easily upload and update photographs of attorneys and add new attorneys names/email hyperlinks as the firm grows. We would like to add developments in the law or success stories easily and quickly, such as through a blog page. On the "Connect With Us" page the website should have hyperlinks to email the Firm, and there should be hyperlinks to email each professional on the "Professionals" page. The website should be viewable on mobile devices without distortion. The law firm focuses on trial work and should have some imagery associated with courtrooms, but the overall theme of the site should be modern, clean, and communicate sophistication and strength. The website should be made in Wordpress. We have uploaded logo files for Haverlock Trial Firm.

Target Market(s)

Corporations and companies that are looking for legal representation. Other attorneys/legal industry.

Industry/Entity Type

Legal Industry

Coding

Coded - Design and coding required

Number of Pages Required

1 page

Font styles to use
Sans Serif

Requirements
Must have
• Simple, clean, sophisticated, modern website that includes the logo, watermark of logo, and the elements described above.
Nice to have
• Pictures of city scape, buildings, courtroom, team members.

```html
<!DOCTYPE html>
<html lang="en">
<head>
<meta charset="utf-8">
<title>Haverlock Trial Firm PLLC</title>
<link href="https://fonts.googleapis.com/css2?family=PT+Serif:wght@400;700&family=Lato:wght@400;700;900&display=swap" rel="stylesheet">
<style>
:root{
  --blue:#1a73e8;
  --blue-dark:#0d5bc6;
  --ink:#111111;
  --text:#333333;
  --muted:#777777;
  --light:#f4f4f4;
  --white:#ffffff;
  --black:#050505;
  --footer:#0b0b0b;
}
*{box-sizing:border-box;margin:0;padding:0}
html,body{width:1200px;height:3840px;overflow:hidden}
body{font-family:'Lato',Arial,sans-serif;color:var(--text);background:var(--white);position:relative}
.btn{display:inline-block;background:var(--blue);color:var(--white);font-weight:700;font-size:15px;padding:11px 22px;border-radius:4px;text-decoration:none}
.section-title{font-family:'PT Serif',Georgia,serif;font-size:46px;font-weight:400;color:var(--ink);text-align:center}
.section-title b{font-weight:700}

/* hero */
.hero{position:absolute;top:0;left:0;width:1200px;height:660px;overflow:hidden}
.hero-photo{position:absolute;inset:0;background:linear-gradient(100deg,#1b1512 0%,#3a2b22 35%,#6b5140 60%,#8a7663 80%,#4a3d33 100%)}
.hero-shade{position:absolute;inset:0;background:linear-gradient(90deg,rgba(0,0,0,.78) 0%,rgba(0,0,0,.45) 45%,rgba(0,0,0,.1) 100%)}
.nav{position:absolute;top:0;left:0;width:1200px;height:120px;display:flex;align-items:flex-start;justify-content:space-between;padding:12px 40px 0 112px}
.brand{display:flex;align-items:center;gap:12px;color:var(--white);font-family:'Lato',Arial,sans-serif;font-weight:900;font-size:24px;letter-spacing:2px;line-height:1.05;text-transform:uppercase}
.brand-square{width:46px;height:46px;background:var(--white)}
.menu{display:flex;gap:22px;align-items:center;padding-top:4px}
.menu a{color:var(--white);font-size:14px;font-weight:700;text-decoration:none;padding-bottom:4px}
.menu a.active{border-bottom:2px solid var(--blue)}
.menu .btn{padding:7px 14px;font-size:14px}
.hero-copy{position:absolute;left:112px;top:220px;width:560px;color:var(--white)}
.hero-copy h1{font-family:'PT Serif',Georgia,serif;font-size:54px;line-height:64px;font-weight:700}
.hero-copy p{font-size:17px;font-weight:700;margin:16px 0 22px}

/* practices */
.practices{position:absolute;top:660px;left:0;width:1200px;height:560px;background:var(--white)}
.practices .section-title{position:absolute;top:52px;width:100%}
.practice-row{position:absolute;top:160px;left:96px;display:flex;gap:32px}
.practice-card{position:relative;width:228px;height:250px;background:var(--white);box-shadow:0 4px 18px rgba(0,0,0,.14);text-align:center;padding:86px 20px 0}
.practice-icon{position:absolute;top:14px;left:50%;transform:translateX(-50%);width:60px;height:60px;border-radius:50%;background:var(--blue);display:flex;align-items:center;justify-content:center}
.practice-card h3{font-family:'PT Serif',Georgia,serif;font-size:20px;font-weight:400;color:var(--ink)}
.practice-card p{font-size:12px;color:var(--muted);line-height:1.5;margin-top:10px}
.practice-card .arrow{position:absolute;bottom:22px;left:50%;transform:translateX(-50%)}
.practices .btn{position:absolute;top:455px;left:552px}

/* about */
.about{position:absolute;top:1220px;left:0;width:1200px;height:420px;background:var(--black);overflow:hidden}
.about-copy{position:absolute;left:112px;top:60px;width:420px;color:var(--white)}
.about-copy h2{font-family:'PT Serif',Georgia,serif;font-size:46px;font-weight:400}
.about-copy p{font-size:13px;line-height:1.7;color:#d8d8d8;margin:14px 0 20px}
.about-mark{position:absolute;right:60px;top:160px;width:500px;text-align:right;color:var(--white);font-family:'Lato',Arial,sans-serif;font-weight:900;font-size:76px;line-height:1;letter-spacing:2px;white-space:nowrap}

/* industries */
.industries{position:absolute;top:1640px;left:0;width:1200px;height:660px}
.industries .section-title{position:absolute;top:62px;width:100%}
.industry-row{position:absolute;top:152px;left:112px;display:flex;gap:32px}
.industry-card{position:relative;width:320px;height:380px;border-radius:6px;overflow:hidden}
.industry-card .photo{position:absolute;inset:0}
.industry-card h3{position:absolute;left:0;right:0;bottom:24px;text-align:center;font-family:'PT Serif',Georgia,serif;font-size:26px;color:var(--white);font-weight:700}
.industry-card.featured h3{top:90px;bottom:auto}
.industry-card.featured p{position:absolute;top:136px;left:40px;right:40px;text-align:center;color:var(--white);font-size:15px;line-height:1.45}
.industries .btn{position:absolute;top:570px;left:552px}

/* testimonials */
.testimonials{position:absolute;top:2300px;left:0;width:1200px;height:540px;overflow:hidden}
.testimonials .bg{position:absolute;inset:0;background:linear-gradient(180deg,#1e1e1e 0%,#3a3a3a 45%,#262626 100%)}
.testimonials h2{position:absolute;top:90px;left:112px;font-family:'PT Serif',Georgia,serif;font-size:46px;font-weight:400;color:var(--white)}
.slider-arrows{position:absolute;top:100px;right:112px;display:flex;gap:6px}
.slider-arrows span{width:26px;height:26px;border-radius:50%;background:var(--white);display:flex;align-items:center;justify-content:center}
.testimonial-row{position:absolute;top:180px;left:112px;display:flex;gap:40px}
.testimonial{position:relative;width:468px;height:260px;background:var(--white);border-radius:6px;padding:26px 28px}
.testimonial::after{content:"";position:absolute;bottom:-24px;left:50%;margin-left:-14px;border-left:28px solid transparent;border-top:24px solid var(--white)}
.t-head{display:flex;align-items:center;gap:16px}
.avatar{width:60px;height:60px;border-radius:50%;background:#8a8f96}
.t-head strong{font-size:16px;color:var(--ink);flex:1}
.quote{font-family:'PT Serif',Georgia,serif;font-size:52px;font-weight:700;color:var(--blue);line-height:1;height:36px}
.testimonial p{font-size:13px;line-height:1.65;color:var(--muted);margin-top:18px}
.testimonial a{display:block;margin-top:14px;font-size:13px;color:var(--blue)}

/* stories */
.stories{position:absolute;top:2840px;left:0;width:1200px;height:720px}
.stories .section-title{position:absolute;top:56px;width:100%}
.story-row{position:absolute;top:140px;left:112px;display:flex;gap:32px}
.story{width:320px;height:440px;background:var(--white);box-shadow:0 4px 18px rgba(0,0,0,.12)}
.story .photo{height:240px}
.story-body{padding:20px 22px}
.story .cat{font-size:14px;color:var(--blue);font-weight:700}
.story h3{font-family:'PT Serif',Georgia,serif;font-size:19px;font-weight:400;color:var(--ink);line-height:1.35;margin-top:10px;height:78px;overflow:hidden}
.story .meta{display:flex;gap:22px;margin-top:12px;font-size:12px;color:var(--muted);align-items:center}
.story .meta span{display:flex;align-items:center;gap:6px}
.stories .btn{position:absolute;top:634px;left:552px}

/* footer */
.footer{position:absolute;top:3560px;left:0;width:1200px;height:280px;background:var(--footer);color:var(--white)}
.footer-brand{position:absolute;left:112px;top:40px}
.footer-brand .brand{font-size:28px}
.socials{display:flex;gap:10px;margin-top:24px}
.socials span{width:26px;height:26px;border-radius:50%;background:var(--white)}
.footer-col{position:absolute;top:28px}
.footer-col h4{font-family:'PT Serif',Georgia,serif;font-size:22px;font-weight:400;margin-bottom:10px}
.footer-col a{display:block;color:#e0e0e0;font-size:12px;text-decoration:none;line-height:20px}
.contact-line{display:flex;align-items:center;gap:10px;font-size:12px;color:#e0e0e0;margin-bottom:18px}
.contact-line i{width:24px;height:24px;border-radius:50%;background:var(--white);display:flex;align-items:center;justify-content:center}
.copyright{position:absolute;bottom:0;left:0;width:100%;height:36px;border-top:1px solid #2a2a2a;text-align:center;font-size:12px;line-height:36px;color:#cccccc}
</style>
</head>
<body>

<header class="hero">
  <div class="hero-photo" role="img" aria-label="Photo of two attorneys reviewing documents in a modern office"></div>
  <div class="hero-shade"></div>
  <nav class="nav">
    <div class="brand"><span class="brand-square"></span><span>Haverlock<br>Trial Firm</span></div>
    <div class="menu">
      <a href="#" class="active">Home</a>
      <a href="#">About</a>
      <a href="#">Practice Areas</a>
      <a href="#">Professionals</a>
      <a href="#">Blog</a>
      <a href="#">Resources &amp; Advisories</a>
      <a href="#" class="btn">Contact Us</a>
    </div>
  </nav>
  <div class="hero-copy">
    <h1>Your Trusted Partner in High-Stakes Litigation</h1>
    <p>Experienced Attorneys Delivering Results in Florida's Courtrooms</p>
    <a href="#" class="btn">Contact With Us</a>
  </div>
</header>

<section class="practices">
  <h2 class="section-title">Areas of <b>Pratices</b></h2>
  <div class="practice-row">
    <article class="practice-card">
      <div class="practice-icon"><svg width="28" height="28" viewBox="0 0 24 24" fill="none" stroke="#fff" stroke-width="2"><rect x="4" y="7" width="16" height="13" rx="1"/><path d="M9 7V4h6v3"/></svg></div>
      <h3>Product liability</h3>
      <p>Lorem ipsum dolor sit amet, consectetur adipiscing elit.</p>
      <svg class="arrow" width="20" height="12" viewBox="0 0 20 12" fill="none" stroke="#111" stroke-width="2"><path d="M0 6h18M13 1l5 5-5 5"/></svg>
    </article>
    <article class="practice-card">
      <div class="practice-icon"><svg width="28" height="28" viewBox="0 0 24 24" fill="none" stroke="#fff" stroke-width="2"><path d="M3 21h18M5 21V9l7-5 7 5v12"/><rect x="10" y="14" width="4" height="7"/></svg></div>
      <h3>Premises liability</h3>
      <p>Lorem ipsum dolor sit amet, consectetur adipiscing elit.</p>
      <svg class="arrow" width="20" height="12" viewBox="0 0 20 12" fill="none" stroke="#111" stroke-width="2"><path d="M0 6h18M13 1l5 5-5 5"/></svg>
    </article>
    <article class="practice-card">
      <div class="practice-icon"><svg width="28" height="28" viewBox="0 0 24 24" fill="none" stroke="#fff" stroke-width="2"><path d="M4 16a8 8 0 0 1 16 0"/><path d="M2 16h20v3H2z"/><path d="M12 8v4"/></svg></div>
      <h3>Construction defects</h3>
      <p>Lorem ipsum dolor sit amet, consectetur adipiscing elit.</p>
      <svg class="arrow" width="20" height="12" viewBox="0 0 20 12" fill="none" stroke="#111" stroke-width="2"><path d="M0 6h18M13 1l5 5-5 5"/></svg>
    </article>
    <article class="practice-card">
      <div class="practice-icon"><svg width="28" height="28" viewBox="0 0 24 24" fill="none" stroke="#fff" stroke-width="2"><path d="M3 5h12v9H8l-5 4z"/><path d="M15 9h6v9l-4-3h-6"/></svg></div>
      <h3>Commercial disputes</h3>
      <p>Lorem ipsum dolor sit amet, consectetur adipiscing elit.</p>
      <svg class="arrow" width="20" height="12" viewBox="0 0 20 12" fill="none" stroke="#111" stroke-width="2"><path d="M0 6h18M13 1l5 5-5 5"/></svg>
    </article>
  </div>
  <a href="#" class="btn">View All</a>
</section>

<section class="about">
  <div class="about-copy">
    <h2>About Us</h2>
    <p>Sed ut perspiciatis unde omnis iste natus error sit voluptatem accusantium doloremque laudantium, totam rem aperiam, eaque ipsa quae ab illo inventore veritatis et quasi architecto beatae vitae dicta sunt explicabo. Nemo enim ipsam voluptatem quia voluptas sit aspernatur aut odit aut fugit, sed quia consequuntur magni dolores eos qui ratione voluptatem sequi nesciunt.</p>
    <a href="#" class="btn">Read More</a>
  </div>
  <div class="about-mark">HAVERLOCK</div>
</section>

<section class="industries">
  <h2 class="section-title">Industries <b>We Serve</b></h2>
  <div class="industry-row">
    <article class="industry-card">
      <div class="photo" role="img" aria-label="Photo of a worker operating machinery in a factory" style="background:linear-gradient(160deg,#6d7f92 0%,#2e3d4d 55%,#1a232d 100%)"></div>
      <h3>Manufacturing</h3>
    </article>
    <article class="industry-card featured">
      <div class="photo" role="img" aria-label="Photo of a construction site with workers, tinted blue" style="background:linear-gradient(160deg,#3f8fd6 0%,#1d67b4 55%,#12508f 100%)"></div>
      <h3>Construction</h3>
      <p>Resolving construction defects, project delays, contract disputes, and liability issues in the built environment.</p>
    </article>
    <article class="industry-card">
      <div class="photo" role="img" aria-label="Photo of a freight truck on a highway" style="background:linear-gradient(180deg,#c9d6e2 0%,#9aa9b6 55%,#4d5660 100%)"></div>
      <h3>Transportation</h3>
    </article>
  </div>
  <a href="#" class="btn">View All</a>
</section>

<section class="testimonials">
  <div class="bg" role="img" aria-label="Dark photo of city buildings"></div>
  <h2>Client Testimonials</h2>
  <div class="slider-arrows">
    <span><svg width="10" height="10" viewBox="0 0 10 10" fill="none" stroke="#111" stroke-width="2"><path d="M7 1L3 5l4 4"/></svg></span>
    <span><svg width="10" height="10" viewBox="0 0 10 10" fill="none" stroke="#111" stroke-width="2"><path d="M3 1l4 4-4 4"/></svg></span>
  </div>
  <div class="testimonial-row">
    <article class="testimonial">
      <div class="t-head"><div class="avatar" role="img" aria-label="Client portrait"></div><strong>Evan Thorley</strong><span class="quote">&rdquo;</span></div>
      <p>Neque porro quisquam est, qui dolorem ipsum quia dolor sit amet, consectetur, adipisci velit, sed quia non numquam eius modi tempora incidunt ut labore et dolore magnam aliquam quaerat voluptatem.</p>
      <a href="#">Read More...</a>
    </article>
    <article class="testimonial">
      <div class="t-head"><div class="avatar" role="img" aria-label="Client portrait"></div><strong>Marla Quince</strong><span class="quote">&rdquo;</span></div>
      <p>Neque porro quisquam est, qui dolorem ipsum quia dolor sit amet, consectetur, adipisci velit, sed quia non numquam eius modi tempora incidunt ut labore et dolore magnam aliquam quaerat voluptatem.</p>
      <a href="#">Read More...</a>
    </article>
  </div>
</section>

<section class="stories">
  <h2 class="section-title">Sucess <b>Stories</b></h2>
  <div class="story-row">
    <article class="story">
      <div class="photo" role="img" aria-label="Photo of two professionals reviewing a case at a desk" style="background:linear-gradient(160deg,#e8e4de 0%,#c8bfb3 60%,#9d9185 100%)"></div>
      <div class="story-body">
        <div class="cat">Product liability</div>
        <h3>How We Helped a Manufacturer Win a Major Product Liability Case</h3>
        <div class="meta"><span><svg width="14" height="14" viewBox="0 0 14 14" fill="none" stroke="#777" stroke-width="1.4"><rect x="1" y="2" width="12" height="11"/><path d="M1 5h12"/></svg>Jan 05, 2025</span><span><svg width="14" height="14" viewBox="0 0 14 14" fill="none" stroke="#777" stroke-width="1.4"><path d="M1 2h12v8H5l-4 3z"/></svg>4 Comments</span></div>
      </div>
    </article>
    <article class="story">
      <div class="photo" role="img" aria-label="Photo of a business meeting with colleagues shaking hands" style="background:linear-gradient(160deg,#dfe3e8 0%,#b4bcc6 60%,#7e8893 100%)"></div>
      <div class="story-body">
        <div class="cat">Business Disputes</div>
        <h3>Why Trial Experience Matters in Business Disputes</h3>
        <div class="meta"><span><svg width="14" height="14" viewBox="0 0 14 14" fill="none" stroke="#777" stroke-width="1.4"><rect x="1" y="2" width="12" height="11"/><path d="M1 5h12"/></svg>Jan 19, 2025</span><span><svg width="14" height="14" viewBox="0 0 14 14" fill="none" stroke="#777" stroke-width="1.4"><path d="M1 2h12v8H5l-4 3z"/></svg>4 Comments</span></div>
      </div>
    </article>
    <article class="story">
      <div class="photo" role="img" aria-label="Photo of professionals working on laptops in a bright office" style="background:linear-gradient(160deg,#ece7e0 0%,#cdbfae 60%,#a48f78 100%)"></div>
      <div class="story-body">
        <div class="cat">Product liability</div>
        <h3>How to Protect Your Business from Product Liability Claims</h3>
        <div class="meta"><span><svg width="14" height="14" viewBox="0 0 14 14" fill="none" stroke="#777" stroke-width="1.4"><rect x="1" y="2" width="12" height="11"/><path d="M1 5h12"/></svg>Jan 22, 2025</span><span><svg width="14" height="14" viewBox="0 0 14 14" fill="none" stroke="#777" stroke-width="1.4"><path d="M1 2h12v8H5l-4 3z"/></svg>4 Comments</span></div>
      </div>
    </article>
  </div>
  <a href="#" class="btn">View All</a>
</section>

<footer class="footer">
  <div class="footer-brand">
    <div class="brand"><span class="brand-square"></span><span>Haverlock<br>Trial Firm</span></div>
    <div class="socials"><span></span><span></span><span></span><span></span></div>
  </div>
  <div class="footer-col" style="left:468px">
    <h4>Quick Links</h4>
    <a href="#">Home</a><a href="#">About</a><a href="#">Practice Areas</a><a href="#">Professionals</a><a href="#">Blog</a><a href="#">Resources &amp; Advisories</a><a href="#">Contact</a>
  </div>
  <div class="footer-col" style="left:640px">
    <h4>Help Links</h4>
    <a href="#">Privacy Policy</a><a href="#">Terms &amp; Conditions</a><a href="#">FAQ's</a><a href="#">Support</a><a href="#">Disclaimer</a>
  </div>
  <div class="footer-col" style="left:840px">
    <h4>Contact Info</h4>
    <div class="contact-line"><i><svg width="12" height="12" viewBox="0 0 12 12" fill="#111"><path d="M6 0a4 4 0 0 0-4 4c0 3 4 8 4 8s4-5 4-8a4 4 0 0 0-4-4zm0 5.5A1.5 1.5 0 1 1 6 2.5a1.5 1.5 0 0 1 0 3z"/></svg></i>Lorem Ipsum,USA - 437916</div>
    <div class="contact-line"><i><svg width="12" height="12" viewBox="0 0 12 12" fill="#111"><path d="M2.5 0l2 2.5-1.2 1.5a7 7 0 0 0 4.7 4.7l1.5-1.2 2.5 2-1.5 2.5C5 12 0 7 0 1.5z"/></svg></i>+1 000 000 0000</div>
    <div class="contact-line"><i><svg width="12" height="10" viewBox="0 0 12 10" fill="none" stroke="#111" stroke-width="1.4"><rect x="0.7" y="0.7" width="10.6" height="8.6"/><path d="M1 1l5 4 5-4"/></svg></i>info@haverlocktrial.com</div>
  </div>
  <div class="copyright">&copy; 2025 Haverlock Trial Firm PLLC. All rights reserved.</div>
</footer>

</body>
</html>
```